Corporate Business Card

Very professional, Modern, Not to busy, include phone address email, website
(541) 617-4930, 18761 52nd Avenue S, Corliss, OR 98047, martin@plumlinegroup.com, varkoworks.com

Target Market(s)

Manufacturing

Industry/Entity Type

Aero, machining, manufacturing, Off road racing

Contact Information for Business Card

Phone, address email, website

```html
<!DOCTYPE html>
<html lang="en">
<head>
<meta charset="utf-8">
<title>Varko Works – Business Card</title>
<link href="https://fonts.googleapis.com/css2?family=Roboto:wght@400;900&family=Orbitron:wght@800&display=swap" rel="stylesheet">
<style>
  :root {
    --backdrop: #2a2a2a;
    --navy: #2a3a6b;
    --red: #b52126;
    --white: #f2f2f2;
    --steel: #1c1f27;
  }
  * { margin: 0; padding: 0; box-sizing: border-box; }
  html, body { width: 1200px; height: 1138px; overflow: hidden; }
  body {
    background: var(--backdrop);
    font-family: "Roboto", Arial, sans-serif;
    position: relative;
  }
  .card {
    position: absolute;
    width: 622px;
    height: 375px;
    background: var(--navy);
    border-radius: 16px;
    overflow: hidden;
    box-shadow: 0 4px 10px rgba(0,0,0,0.35);
  }
  .card--front { left: 274px; top: 186px; }
  .card--back  { left: 276px; top: 608px; }

  .brand-name {
    position: absolute;
    left: 0; right: 0;
    text-align: center;
    font-family: "Roboto", Arial, sans-serif;
    font-weight: 900;
    letter-spacing: 1px;
    line-height: 1;
    white-space: nowrap;
  }
  .card--front .brand-name { top: 136px; font-size: 56px; color: var(--steel); }
  .card--back .brand-name  { top: 80px;  font-size: 40px; color: var(--white); }

  .front-url {
    position: absolute;
    left: 0; right: 0;
    top: 326px;
    text-align: center;
    font-size: 17px;
    letter-spacing: 11px;
    color: var(--white);
  }
  .front-url .accent { color: var(--red); }

  .contact-band {
    position: absolute;
    left: 0; right: 0;
    top: 190px;
    height: 108px;
    background: var(--red);
  }
  .person-name {
    position: absolute;
    left: 60px;
    top: 39px;
    font-family: "Orbitron", "Roboto", sans-serif;
    font-weight: 800;
    font-size: 23px;
    color: var(--white);
    letter-spacing: 0.5px;
    white-space: nowrap;
  }
  .contact-list {
    position: absolute;
    left: 288px;
    top: 16px;
    list-style: none;
  }
  .contact-list li {
    display: flex;
    align-items: center;
    height: 25px;
    font-size: 17px;
    color: var(--white);
    white-space: nowrap;
  }
  .contact-list svg { width: 15px; height: 15px; margin-right: 16px; fill: var(--white); }
  .address {
    position: absolute;
    left: 0; right: 0;
    top: 325px;
    text-align: center;
    font-size: 17px;
    color: var(--white);
  }
</style>
</head>
<body>
  <section class="card card--front">
    <div class="brand-name">VARKO WORKS</div>
    <div class="front-url">www.varko<span class="accent">works</span>.com</div>
  </section>

  <section class="card card--back">
    <div class="brand-name">VARKO WORKS</div>
    <div class="contact-band">
      <div class="person-name">MARTIN HALE</div>
      <ul class="contact-list">
        <li>
          <svg viewBox="0 0 16 16" aria-hidden="true"><path d="M1 6c0-2 3-3 7-3s7 1 7 3v1h-3V5.5H4V7H1z"/><path d="M3 8l2-2h6l2 2v6H3z"/></svg>
          (541) 617-4930
        </li>
        <li>
          <svg viewBox="0 0 16 16" aria-hidden="true"><path d="M1 3h14v10H1z M2.5 4.5v0.3L8 9l5.5-4.2v-0.3z M2.5 11.5h11V6.5L8 10.7 2.5 6.5z" fill-rule="evenodd"/></svg>
          martin@plumlinegroup.com
        </li>
        <li>
          <svg viewBox="0 0 16 16" aria-hidden="true"><path fill-rule="evenodd" d="M8 1a7 7 0 1 1 0 14A7 7 0 0 1 8 1zm-.6 1.6C6.3 3.8 5.7 5.3 5.6 7.3h1.8zm1.2 0v4.7h1.8c-.1-2-.7-3.5-1.8-4.7zM4.4 7.3c.1-1.8.6-3.3 1.4-4.3A5.7 5.7 0 0 0 2.3 7.3zm7.2 0h2.1a5.7 5.7 0 0 0-3.5-4.3c.8 1 1.300 2.5 1.4 4.3zM2.3 8.7a5.7 5.7 0 0 0 3.5 4.3c-.8-1-1.3-2.5-1.4-4.3zm3.3 0c.1 2 .7 3.5 1.8 4.7V8.7zm3 0v4.7c1.1-1.2 1.7-2.7 1.8-4.7zm3 0c-.1 1.8-.6 3.3-1.4 4.3a5.7 5.7 0 0 0 3.5-4.3z"/></svg>
          www.varkoworks.com
        </li>
      </ul>
    </div>
    <div class="address">18761 52nd Avenue S, Corliss, OR 98047</div>
  </section>
</body>
</html>
```